New Fun, Positive, energised looking Business Card Needed for High Achiever Coach

I am looking for a two sided full colour business card. I am self employed and have recently re branded my 1-2-1 work re-vitalising high achievers. My target client base for these cards is therefore high achievers - usually aged 40 -55, they are often entrepreneurs, CEO or work in banking and finance and 2/3 are male. I work with them on 90 day or 6 month coaching programs to help them live their success in a healthier, more sustainable and fulfiiled way. They pay for this privately so though they are corporate types the cards need not look 'corporate'. I want to portray the idea of transformation, vitality and re-connecting.
You can get a feel for the look I like on my new website: morvenlisk.co.uk
I want to use this logo with strapline (Re-Vitalising High Achievers) (I purchased off Logoharbor) and font/ colours (the turquoise and green).
Details to include on the card:
www.morvenlisk.co.uk
+44 7915 302618
morven@morvenlisk.co.uk
skype: morvenlisk
I'd also like to include:
Do you struggle to switch off? Want to be healthier and feel fitter? Want closer relationships? More clarity over the direction you are headed? I can help you do these things using integrated mind-body techniques. Visit morvenlisk.co.uk TODAY to apply for a FREE Breakthrough session.
BUT if that is too much text for a card I am open to advice/ammendments.
Updates
Thanks for your design - I am considering them. PLease change the wording to :

```html
<!DOCTYPE html>
<html lang="en">
<head>
<meta charset="utf-8">
<title>Morven Lisk – Business Card</title>
<link rel="stylesheet" href="https://fonts.googleapis.com/css2?family=Open+Sans:ital,wght@0,400;0,600;0,700;1,400&display=swap">
<style>
  :root {
    --turquoise: #14a3c9;
    --turquoise-deep: #0f93b8;
    --green: #4cb66a;
    --white: #ffffff;
    --stage: #eef1f3;
    --ink-shadow: rgba(20, 40, 60, 0.18);
  }
  * { box-sizing: border-box; margin: 0; padding: 0; }
  html, body {
    width: 1200px; height: 720px; overflow: hidden;
    background: var(--stage);
    font-family: "Open Sans", Arial, sans-serif;
  }
  .canvas {
    position: relative; width: 1200px; height: 720px;
    display: flex; align-items: center; justify-content: center; gap: 40px;
  }
  .card {
    position: relative; width: 540px; height: 310px;
    border-radius: 4px; overflow: hidden;
    box-shadow: 0 8px 24px var(--ink-shadow);
  }

  /* Front side */
  .card--front { background: var(--white); }
  .card__wave { position: absolute; inset: 0; width: 100%; height: 100%; }
  .brand {
    position: absolute; left: 70px; top: 56px; width: 260px;
    text-align: center;
  }
  .brand__mark {
    display: inline-block; width: 14px; height: 14px; border-radius: 50%;
    background: var(--green); vertical-align: middle; margin-right: 10px;
  }
  .brand__name {
    display: inline-block; vertical-align: middle;
    font-weight: 700; font-size: 34px; color: var(--turquoise); letter-spacing: 0.5px;
  }
  .brand__tagline {
    margin-top: 2px; font-size: 14px; color: var(--turquoise-deep);
  }
  .contacts {
    position: absolute; left: 178px; top: 224px; right: 16px;
    color: var(--white); font-size: 13.5px; line-height: 1;
  }
  .contacts__row { display: flex; gap: 22px; margin-bottom: 14px; }
  .contact { display: flex; align-items: center; gap: 6px; white-space: nowrap; }
  .contact__icon { width: 13px; height: 13px; flex: none; }

  /* Back side */
  .card--back {
    background: var(--turquoise);
    display: flex; align-items: center; justify-content: center;
  }
  .pitch {
    width: 470px; text-align: center; color: var(--white);
    font-size: 16px; line-height: 1.32;
  }
  .pitch p + p { margin-top: 10px; }
  .pitch strong { font-weight: 700; }
</style>
</head>
<body>
<main class="canvas">

  <section class="card card--front" aria-label="Business card front">
    <svg class="card__wave" viewBox="0 0 540 310" preserveAspectRatio="none" aria-hidden="true">
      <path d="M0,262 C120,200 300,160 540,140 L540,310 L0,310 Z" fill="var(--turquoise)"/>
      <path d="M0,257 C120,195 300,155 540,135" fill="none" stroke="var(--green)" stroke-width="3"/>
    </svg>

    <div class="brand">
      <span class="brand__mark" aria-hidden="true"></span><span class="brand__name">Morven Lisk</span>
      <p class="brand__tagline">Re-Vitalising High Achievers</p>
    </div>

    <div class="contacts">
      <div class="contacts__row">
        <span class="contact">
          <svg class="contact__icon" viewBox="0 0 16 16" aria-hidden="true"><circle cx="8" cy="8" r="8" fill="var(--white)"/><path d="M5.4 4.2l1.3 1.8-.8 1c.5 1 1.3 1.9 2.3 2.3l1-.8 1.8 1.3-.7 1.4c-2.9-.3-5.3-2.7-5.6-5.6z" fill="var(--turquoise)"/></svg>
          +44 7915 302618
        </span>
        <span class="contact">
          <svg class="contact__icon" viewBox="0 0 16 16" aria-hidden="true"><rect x="1" y="3.5" width="14" height="9" rx="1" fill="var(--white)"/><path d="M1.5 4l6.5 5 6.5-5" fill="none" stroke="var(--turquoise)" stroke-width="1.3"/></svg>
          morven@morvenlisk.co.uk
        </span>
      </div>
      <div class="contacts__row">
        <span class="contact">
          <svg class="contact__icon" viewBox="0 0 16 16" aria-hidden="true"><circle cx="8" cy="8" r="7" fill="none" stroke="var(--white)" stroke-width="1.5"/><ellipse cx="8" cy="8" rx="3" ry="7" fill="none" stroke="var(--white)" stroke-width="1.2"/><path d="M1 8h14" stroke="var(--white)" stroke-width="1.2"/></svg>
          www.morvenlisk.co.uk
        </span>
        <span class="contact">
          <svg class="contact__icon" viewBox="0 0 16 16" aria-hidden="true"><circle cx="8" cy="8" r="7" fill="var(--white)"/></svg>
          morvenlisk
        </span>
      </div>
    </div>
  </section>

  <section class="card card--back" aria-label="Business card back">
    <div class="pitch">
      <p>Do you struggle to switch off?<br>
         Want to be healthier and feel fitter?<br>
         Want closer relationships?<br>
         More clarity over the direction you are headed?</p>
      <p>I can help you do these things using integrated<br>mind-body techniques.</p>
      <p>Visit <strong>morvenlisk.co.uk</strong> TODAY to apply for a<br>FREE Breakthrough session.</p>
    </div>
  </section>

</main>
</body>
</html>
```